Build a landing page to promote a service (dialler consultation and support).

We are a call centre consultation firm and we need a landing page to promote a service. The service is Tormalux dialler consultation and support.
If you do not know what Tormalux is, please do some quick "Zorvex" research for more information.
The landing page will be promoted with a paid advertisement, so we want something that is simple, and explains exactly what service we offer.
There are two objectives for the landing page:
1) A "call to action" which directs the user to a contact page, including a form plus all of our contact details.
2) A form for them viewers to enter their details to get a "FREE" quote for their project. This form should be placed on the main page.
Notes:
The call to action will require the viewer to enter their name, email, phone number as well as a description of their request. There will also need to be a drop down menu for the type of quote. This menu should have the following options:
1) Tormalux support
2) Tormalux hosting
3) Tormalux customisation
4) Other
We need 2 pages in total:
1) Main landing page
This is the home page. It will need to clearly indicate our services and our key selling features.
Services:
* Tormalux support
* Tormalux hosting
* Tormalux customisation
Key Selling Features:
* Australian based
* PCI complaint
* 10+ years of dialler and call centre experience
* we run a sister company which is a highly reputable 40 seat call centre, so we know first hand about call centre technology.
The main landing page will have an "about us" section with a few paragraphs about how we got started.
-------------------------------------------------------------------------
2) Contact page
All of our contact details will live on this page, as well as a contact form.
Other notes:
We will be self hosting the landing page.
We already have a domain name.
The design must be clean and incorporate our logo, as well as it's colours. (Logo attached)
We want a fully function HTML landing page, not just a "PSD" design.
The page must be mobile optimised.
Anyone using Tormalux software.

```html
<!DOCTYPE html>
<html lang="en">
<head>
<meta charset="utf-8">
<title>Quellora – Call Centre Consultation</title>
<link rel="stylesheet" href="https://fonts.googleapis.com/css2?family=Poppins:wght@400;500;600&family=Roboto+Condensed:wght@400;500&family=Open+Sans:wght@400;600&display=swap">
<style>
:root{
  --teal:#33a78c;
  --blue:#2a8bd2;
  --ink:#1c1c1c;
  --text:#555;
  --line:#9a9a9a;
  --footer:#0e0e0e;
  --white:#fff;
}
*{box-sizing:border-box;margin:0;padding:0}
html,body{width:1200px;height:3025px;overflow:hidden}
body{position:relative;background:var(--white);font-family:"Open Sans",sans-serif;color:var(--ink)}
.abs{position:absolute}
a{color:inherit;text-decoration:none}

/* header */
.header{left:0;top:0;width:1200px;height:100px;background:var(--white);border-top:5px solid var(--teal);z-index:5;box-shadow:0 2px 6px rgba(0,0,0,.08)}
.brand{left:88px;top:14px;display:flex;flex-direction:column;align-items:center;gap:4px}
.brand-dot{width:46px;height:46px;border-radius:50%;background:var(--blue)}
.brand-name{font-family:"Poppins",sans-serif;font-weight:500;font-size:22px;color:var(--blue)}
.nav{right:95px;top:36px;display:flex;gap:40px;font-family:"Poppins",sans-serif;font-size:17px;color:#222}
.nav .active{color:var(--blue)}

/* hero */
.hero{left:0;top:100px;width:1200px;height:645px}
.hero-title{left:93px;top:412px;font-family:"Roboto Condensed",sans-serif;font-size:92px;color:#fff;line-height:1}
.hero-sub{left:96px;top:520px;font-family:"Roboto Condensed",sans-serif;font-size:40px;color:#fff}
.hero-arrows{left:105px;top:598px;display:flex;gap:14px}

/* quick contact */
.quick{left:773px;top:250px;width:338px;height:488px;background:#fff;border-bottom:7px solid var(--teal);box-shadow:0 4px 14px rgba(0,0,0,.15);z-index:4}
.quick::before{content:"";position:absolute;left:0;top:28px;width:4px;height:34px;background:var(--blue)}
.quick h3{position:absolute;top:30px;width:100%;text-align:center;font-family:"Poppins",sans-serif;font-weight:400;font-size:23px;color:#222}
.field{position:absolute;left:37px;width:262px;height:38px;border:1px solid #888;border-radius:19px;font-family:"Poppins",sans-serif;font-size:14px;color:#333;padding:8px 17px}
.field svg{position:absolute;right:16px;top:15px}
.submit{position:absolute;left:87px;top:395px;width:152px;height:40px;border-radius:20px;background:linear-gradient(90deg,var(--teal),var(--blue));color:#fff;font-family:"Poppins",sans-serif;font-weight:600;font-size:16px;text-align:center;line-height:40px;box-shadow:0 8px 14px rgba(51,167,140,.35)}

/* shared */
.photo-frame{border:3px solid #111}
.photo{box-shadow:0 4px 12px rgba(0,0,0,.25)}
.section-title{font-family:"Poppins",sans-serif;font-weight:400;color:#111}
.btn{display:inline-block;height:36px;line-height:36px;padding:0 21px;border-radius:18px;background:linear-gradient(90deg,var(--teal),var(--blue));color:#fff;font-family:"Poppins",sans-serif;font-size:16px;box-shadow:0 8px 14px rgba(51,167,140,.3)}

/* about */
.about-text{left:557px;top:916px;width:535px;font-size:14.3px;line-height:25px;color:var(--text)}

/* services */
.services-title{left:0;top:1380px;width:1200px;text-align:center;font-family:"Poppins",sans-serif;font-weight:500;font-size:42px;color:#fff}
.card{top:1535px;width:313px;height:300px;background:#fff;text-align:center;box-shadow:0 3px 10px rgba(0,0,0,.12)}
.card .icon{position:absolute;left:91px;top:-62px;width:131px;height:131px;border-radius:50%;border:5px solid var(--teal);background:#fff;display:flex;align-items:center;justify-content:center}
.card .icon span{width:112px;height:112px;border-radius:50%;background:linear-gradient(135deg,#2f97d6,#1f78c4);display:flex;align-items:center;justify-content:center}
.card h4{margin-top:92px;font-family:"Poppins",sans-serif;font-weight:500;font-size:21px;color:#111}
.card p{margin:18px auto 0;width:230px;font-size:14.5px;line-height:25px;color:var(--text)}
.card .outline{display:inline-block;margin-top:28px;padding:0 22px;height:34px;line-height:32px;border:1.5px solid #333;border-radius:17px;font-family:"Poppins",sans-serif;font-size:14px;color:#222}
.card .filled{display:inline-block;margin-top:28px;padding:0 24px;height:34px;line-height:34px;border-radius:17px;background:linear-gradient(90deg,var(--teal),var(--blue));color:#fff;font-family:"Poppins",sans-serif;font-size:14px;box-shadow:0 8px 14px rgba(51,167,140,.3)}

/* features */
.features-list{left:98px;top:2236px;width:540px;list-style:none;font-size:14.8px;color:#444;line-height:25px}
.features-list li{position:relative;padding-left:22px;margin-bottom:9px}
.features-list li svg{position:absolute;left:0;top:5px}

/* footer */
.footer-brand{left:100px;top:2728px;display:flex;flex-direction:column;align-items:center;gap:12px}
.footer-brand .brand-dot{width:84px;height:84px;background:var(--teal)}
.footer-brand .brand-name{font-size:36px;color:var(--blue)}
.fcol{font-family:"Poppins",sans-serif;color:#fff}
.fcol h5{font-weight:400;font-size:21px;margin-bottom:20px}
.fcol ul{list-style:none;font-size:15px;line-height:33px}
.contact-item{position:relative;padding-left:28px;margin-bottom:24px}
.contact-item b{display:block;font-weight:500;font-size:16px}
.contact-item small{font-size:14px}
.contact-item svg{position:absolute;left:0;top:2px}
.copyright{left:0;top:2985px;width:1200px;text-align:center;font-size:13.5px;color:#ccc}
</style>
</head>
<body>

<header class="abs header">
  <a class="abs brand" href="#"><span class="brand-dot"></span><span class="brand-name">Quellora</span></a>
  <nav class="abs nav">
    <a class="active" href="#">Home</a><a href="#">About us</a><a href="#">Services</a><a href="#">Products</a><a href="#">News</a><a href="#">Contact us</a>
  </nav>
</header>

<section class="abs hero">
  <svg width="1200" height="645" role="img" aria-label="Call centre agents wearing headsets working at desks">
    <defs>
      <linearGradient id="heroFill" x1="0" y1="0" x2="1" y2="0.4">
        <stop offset="0" stop-color="#3f3b3c"/><stop offset=".45" stop-color="#7a7270"/><stop offset="1" stop-color="#c9cacd"/>
      </linearGradient>
    </defs>
    <polygon points="0,0 1200,0 1200,640 0,558" fill="url(#heroFill)"/>
  </svg>
  <h1 class="abs hero-title" style="top:312px">Quellora</h1>
  <p class="abs hero-sub" style="top:420px">Call Centre Consultation</p>
  <div class="abs hero-arrows" style="top:498px">
    <svg width="12" height="16"><path d="M9 2 L3 8 L9 14" stroke="#fff" stroke-width="2" fill="none"/></svg>
    <svg width="12" height="16"><path d="M3 2 L9 8 L3 14" stroke="#fff" stroke-width="2" fill="none"/></svg>
  </div>
</section>

<form class="abs quick">
  <h3>Quick Contact</h3>
  <div class="field" style="top:103px">Name</div>
  <div class="field" style="top:158px">Email Id</div>
  <div class="field" style="top:213px">Phone</div>
  <div class="field" style="top:268px">Tormalux support<svg width="11" height="7"><path d="M0 0 H11 L5.5 7Z" fill="#333"/></svg></div>
  <div class="field" style="top:323px">Description</div>
  <div class="submit">SUBMIT</div>
</form>

<!-- about -->
<div class="abs photo-frame" style="left:90px;top:822px;width:412px;height:314px"></div>
<div class="abs photo" role="img" aria-label="Team leader with tablet standing among seated call centre agents" style="left:118px;top:845px;width:400px;height:316px;background:linear-gradient(135deg,#9ea3a6,#d8d5d2 55%,#7b8187)"></div>
<h2 class="abs section-title" style="left:557px;top:848px;font-size:42px">About us</h2>
<p class="abs about-text">It is a long established fact that a reader will be distracted by the readable content of a page when looking at its layout. The point of using Lorem Ipsum is that it has a more-or-less normal distribution of letters, as opposed to using 'Content here, content here', making it look like readable English. Many desktop publishing packages and web page editors now use Lorem Ipsum as their default model text, and a search for 'lorem ipsum' will uncover many</p>
<a class="abs btn" style="left:557px;top:1100px">Read More</a>

<!-- services -->
<svg class="abs" style="left:0;top:1210px" width="1200" height="810" role="img" aria-label="Faded photo of smiling call centre agents behind services">
  <defs>
    <linearGradient id="servFill" x1="0" y1="1" x2="1" y2="0">
      <stop offset="0" stop-color="#37ab88"/><stop offset=".5" stop-color="#2e9bb4"/><stop offset="1" stop-color="#2a8dd3"/>
    </linearGradient>
  </defs>
  <polygon points="0,125 1200,5 1200,670 0,805" fill="url(#servFill)"/>
</svg>
<h2 class="abs services-title">Our Services</h2>

<div class="abs card" style="left:85px">
  <div class="icon"><span><svg width="58" height="58" fill="none" stroke="#fff" stroke-width="2"><circle cx="29" cy="12" r="5"/><path d="M21 24 q8-8 16 0"/><circle cx="12" cy="38" r="5"/><path d="M4 52 q8-8 16 0"/><circle cx="46" cy="38" r="5"/><path d="M38 52 q8-8 16 0"/><path d="M20 20 L14 28 M38 20 L44 28 M22 42 H36"/></svg></span></div>
  <h4>Tormalux support</h4>
  <p>It is a long established fact that a reader will be distracted by the readable content of a page</p>
  <span class="outline">Read more</span>
</div>
<div class="abs card" style="left:430px">
  <div class="icon"><span><svg width="58" height="58" fill="none" stroke="#fff" stroke-width="2"><rect x="5" y="8" width="48" height="32" rx="2"/><path d="M22 40 L20 50 H38 L36 40 M5 34 H53 M24 26 L32 18"/></svg></span></div>
  <h4>Tormalux hosting</h4>
  <p>It is a long established fact that a reader will be distracted by the readable content of a page</p>
  <span class="filled">Read more</span>
</div>
<div class="abs card" style="left:777px">
  <div class="icon"><span><svg width="58" height="58" fill="none" stroke="#fff" stroke-width="2"><path d="M12 32 V26 a17 17 0 0 1 34 0 V32"/><rect x="9" y="30" width="8" height="14" rx="3"/><rect x="41" y="30" width="8" height="14" rx="3"/><path d="M45 44 q0 8 -12 8"/></svg></span></div>
  <h4>Tormalux customisation</h4>
  <p>It is a long established fact that a reader will be distracted by the readable content of a page</p>
  <span class="outline">Read more</span>
</div>

<!-- features -->
<h2 class="abs section-title" style="left:98px;top:2160px;font-size:44px">Key Selling Features:</h2>
<ul class="abs features-list">
  <li><svg width="13" height="13"><circle cx="6.5" cy="6.5" r="6.5" fill="var(--teal)"/><path d="M5 3.5 L8 6.5 L5 9.5" stroke="#fff" stroke-width="1.8" fill="none"/></svg>Australian based</li>
  <li><svg width="13" height="13"><circle cx="6.5" cy="6.5" r="6.5" fill="var(--teal)"/><path d="M5 3.5 L8 6.5 L5 9.5" stroke="#fff" stroke-width="1.8" fill="none"/></svg>PCI complaint</li>
  <li><svg width="13" height="13"><circle cx="6.5" cy="6.5" r="6.5" fill="var(--teal)"/><path d="M5 3.5 L8 6.5 L5 9.5" stroke="#fff" stroke-width="1.8" fill="none"/></svg>10+ years of dialler and call centre experience</li>
  <li><svg width="13" height="13"><circle cx="6.5" cy="6.5" r="6.5" fill="var(--teal)"/><path d="M5 3.5 L8 6.5 L5 9.5" stroke="#fff" stroke-width="1.8" fill="none"/></svg>we run a sister company which is a highly reputable 40 seat call centre, so we know first hand about call centre technology.</li>
</ul>
<a class="abs btn" style="left:98px;top:2415px">Read More</a>
<div class="abs photo-frame" style="left:685px;top:2125px;width:412px;height:316px"></div>
<div class="abs photo" role="img" aria-label="Two call centre agents with headsets at computer screens" style="left:668px;top:2148px;width:400px;height:316px;background:linear-gradient(120deg,#8f9497,#d9d6d3 50%,#4d4f52)"></div>

<!-- footer -->
<svg class="abs" style="left:0;top:2565px" width="1200" height="460" aria-hidden="true">
  <defs>
    <linearGradient id="stripe" x1="0" x2="1"><stop offset="0" stop-color="#33a78c"/><stop offset="1" stop-color="#2a88d2"/></linearGradient>
  </defs>
  <polygon points="0,5 1200,85 1200,100 0,20" fill="url(#stripe)"/>
  <polygon points="0,20 1200,100 1200,460 0,460" fill="var(--footer)"/>
</svg>
<div class="abs footer-brand"><span class="brand-dot"></span><span class="brand-name">Quellora</span></div>

<div class="abs fcol" style="left:426px;top:2715px">
  <h5>CONTACT US</h5>
  <div class="contact-item"><svg width="20" height="15" fill="none" stroke="#fff" stroke-width="1.5"><rect x="1" y="1" width="18" height="13"/><path d="M1 1 L10 8 L19 1"/></svg><b>EMAIL ADDRESS</b><small>info@samplemail.com</small></div>
  <div class="contact-item"><svg width="20" height="20" fill="none" stroke="#fff" stroke-width="1.5"><path d="M4 2 L8 2 L9 7 L6 9 Q8 13 11 15 L13 12 L18 13 L18 17 Q10 19 5 12 Q2 7 4 2Z"/></svg><b>PHONE NUMBER</b><small>(555) 014-2290</small></div>
</div>
<div class="abs fcol" style="left:732px;top:2715px">
  <h5>ABOUT</h5>
  <ul><li>Home</li><li>About Us</li><li>Services</li><li>Products</li></ul>
</div>
<div class="abs fcol" style="left:963px;top:2715px">
  <h5>RESOURCES</h5>
  <ul><li>News</li><li>Support</li><li>Faq</li><li>Contact</li></ul>
</div>
<p class="abs copyright">© 2018 Company Name &nbsp;All right reserved</p>

</body>
</html>
```